Hvac and insulation company needs good looking business card design

We are hvac and insulation company and looking for a new business cards that look to today standards designs

Target Market(s)

homeowners

Industry/Entity Type

Hvac

Contact Information for Business Card

Name: Walter Brinoku
Home comfort consultant
address: 4827 Dunmore St #215 Oakland, CA 94619
office: 888-316-2790
cell: 510-742-3185
Lic.# 584261
Email: walter@corvane-hvac.com
Web: corvane-hvac.com

Requirements
Must have
• clean and sleek look
Nice to have
• simple with a clean look
Should not have
• to busy business card

```html
<!DOCTYPE html>
<html lang="en">
<head>
<meta charset="utf-8">
<title>Corvane Home Solutions – Business Card</title>
<link rel="stylesheet" href="https://fonts.googleapis.com/css2?family=Source+Sans+3:wght@400;700&display=swap">
<style>
  :root {
    --backdrop: #8a5a34;
    --kraft-light: #dcb78c;
    --kraft-mid: #c99c6c;
    --kraft-dark: #b8895a;
    --ink: #231a12;
  }
  * { margin: 0; padding: 0; box-sizing: border-box; }
  html, body { width: 1200px; height: 900px; overflow: hidden; }
  body {
    position: relative;
    background: var(--backdrop);
    font-family: "Source Sans 3", "Myriad Pro", Arial, sans-serif;
    color: var(--ink);
  }
  .card {
    position: absolute;
    left: 330px;
    width: 556px;
    height: 343px;
    background: linear-gradient(160deg, var(--kraft-light) 0%, var(--kraft-mid) 55%, var(--kraft-dark) 100%);
    box-shadow: 3px 4px 8px rgba(0, 0, 0, 0.45);
  }
  .card--back { top: 90px; }
  .card--front { top: 470px; }

  .details {
    position: absolute;
    inset: 0;
    text-align: center;
  }
  .details__name {
    position: absolute; left: 0; right: 0; top: 60px;
    font-size: 19px; font-weight: 400; letter-spacing: 0.3px;
    text-transform: uppercase;
  }
  .details__role {
    position: absolute; left: 0; right: 0; top: 89px;
    font-size: 15px;
  }
  .details__contact {
    position: absolute; left: 0; right: 0; top: 139px;
    list-style: none; font-size: 15px; line-height: 20px;
  }
  .details__address {
    position: absolute; left: 0; right: 0; top: 246px;
    font-size: 15px; font-style: normal;
  }
  .details__license {
    position: absolute; left: 0; right: 0; top: 273px;
    font-size: 15px;
  }

  .brand {
    position: absolute;
    left: 78px; top: 128px;
    display: flex; align-items: center; gap: 22px;
  }
  .brand__mark {
    width: 78px; height: 78px;
    background: var(--ink);
  }
  .brand__words { display: flex; flex-direction: column; }
  .brand__name {
    font-size: 74px; font-weight: 700; line-height: 0.9;
    letter-spacing: 0.5px;
  }
  .brand__tagline {
    font-size: 21px; font-weight: 700; letter-spacing: 2.6px;
    margin-top: 4px;
  }
</style>
</head>
<body>
  <section class="card card--back">
    <div class="details">
      <h1 class="details__name">Walter Brinoku</h1>
      <p class="details__role">Home Comfort Consultant</p>
      <ul class="details__contact">
        <li>888-316-2790</li>
        <li>510-742-3185</li>
        <li>walter@corvane-hvac.com</li>
        <li>corvane-hvac.com</li>
      </ul>
      <address class="details__address">4827 Dunmore St #215 Oakland, CA 94619</address>
      <p class="details__license">Lic.# 584261</p>
    </div>
  </section>

  <section class="card card--front">
    <div class="brand">
      <span class="brand__mark" aria-hidden="true"></span>
      <div class="brand__words">
        <span class="brand__name">corvane</span>
        <span class="brand__tagline">home solutions</span>
      </div>
    </div>
  </section>
</body>
</html>
```